MRT Property - Business Cards

Looking for a business card & general letterhead, signage etc design for our new logo.

Colours:
000a20
0056a2
00b5ef
0088ce
68cef2

Fonts:
Poppins
Karla

Please keep look and feel of new brand - example in the zip package I sent.

```html
<!DOCTYPE html>
<html lang="en">
<head>
<meta charset="utf-8">
<title>MRT Property – Business Cards</title>
<link href="https://fonts.googleapis.com/css2?family=Poppins:wght@400;500;600;700&family=Karla:wght@400;500&display=swap" rel="stylesheet">
<style>
  :root {
    --stage: #1a1a1c;
    --card: #141b2c;
    --card-edge: #0f1523;
    --ink-deep: #000a20;
    --blue: #0056a2;
    --blue-mid: #0088ce;
    --cyan: #00b5ef;
    --sky: #68cef2;
    --steel: #8c8f96;
    --text-light: #e6e9ef;
    --text-soft: #b9c0cc;
  }
  * { box-sizing: border-box; margin: 0; padding: 0; }
  html, body { width: 1200px; height: 852px; overflow: hidden; }
  body {
    background: var(--stage);
    font-family: "Poppins", sans-serif;
    position: relative;
  }
  .card {
    position: absolute;
    left: 320px;
    width: 560px;
    height: 320px;
    border-radius: 22px;
    background: linear-gradient(160deg, #1a2236 0%, var(--card) 55%, var(--card-edge) 100%);
    overflow: hidden;
    box-shadow: 0 18px 40px rgba(0,0,0,.55);
  }
  .card--back { top: 70px; }
  .card--front { top: 460px; }

  /* Back */
  .back-brand {
    position: absolute;
    left: 0; right: 0; top: 110px;
    text-align: center;
    font-weight: 700;
    font-size: 46px;
    letter-spacing: 1px;
    color: var(--steel);
  }
  .back-url {
    position: absolute;
    right: 40px; bottom: 36px;
    font-family: "Karla", sans-serif;
    font-size: 13px;
    letter-spacing: 6px;
    color: var(--text-soft);
  }
  .back-stripe {
    position: absolute;
    left: 0; right: 0; bottom: 0;
    height: 12px;
    background: var(--blue);
  }

  /* Front */
  .front-brand {
    position: absolute;
    left: 40px; top: 50px;
    font-weight: 700;
    font-size: 38px;
    color: var(--blue-mid);
    display: flex; align-items: center; gap: 12px;
  }
  .front-brand .mark {
    width: 16px; height: 16px;
    border-radius: 50%;
    background: var(--cyan);
  }
  .person {
    position: absolute;
    left: 40px; top: 160px;
  }
  .person-name {
    font-weight: 600;
    font-size: 22px;
    color: var(--blue-mid);
    line-height: 1.1;
  }
  .person-role {
    font-size: 12px;
    color: var(--text-soft);
    margin-top: 2px;
  }
  .contact-list {
    position: absolute;
    left: 40px; top: 222px;
    list-style: none;
  }
  .contact-list li {
    display: flex; align-items: center; gap: 14px;
    font-size: 14px;
    color: var(--text-light);
    height: 22px;
  }
  .contact-list svg { width: 14px; height: 14px; fill: var(--text-soft); }
  .address-tab {
    position: absolute;
    right: 0; top: 178px;
    width: 270px; height: 54px;
    background: var(--blue);
    border-radius: 22px 0 0 0;
    color: var(--text-light);
    font-size: 13px;
    display: flex; align-items: center;
    padding-left: 26px;
  }
  .front-stripes { position: absolute; left: 0; bottom: 0; width: 560px; height: 100px; }
</style>
</head>
<body>

<section class="card card--back" aria-label="Business card back">
  <div class="back-brand">MRT Property</div>
  <div class="back-url">www.mrtproperty.com</div>
  <div class="back-stripe"></div>
</section>

<section class="card card--front" aria-label="Business card front">
  <div class="front-brand"><span>MRT Property</span><span class="mark"></span></div>

  <div class="person">
    <div class="person-name">Callum Reyes</div>
    <div class="person-role">Associate Director</div>
  </div>

  <ul class="contact-list">
    <li>
      <svg viewBox="0 0 24 24"><path d="M6.6 10.8a15.1 15.1 0 0 0 6.6 6.6l2.2-2.2c.3-.3.7-.4 1-.2 1.1.4 2.3.6 3.6.6.6 0 1 .4 1 1V20c0 .6-.4 1-1 1A17 17 0 0 1 3 4c0-.6.4-1 1-1h3.5c.6 0 1 .4 1 1 0 1.3.2 2.5.6 3.6.1.3 0 .7-.2 1z"/></svg>
      <span>555-204-3318</span>
    </li>
    <li>
      <svg viewBox="0 0 24 24"><path d="M2 5h20v14H2zm2 2v.5l8 5 8-5V7l-8 5z"/></svg>
      <span>callum@mrtproperty.com</span>
    </li>
    <li>
      <svg viewBox="0 0 24 24"><path d="M12 2a10 10 0 1 0 0 20 10 10 0 0 0 0-20zm6.9 9h-3a15 15 0 0 0-1.2-5.6A8 8 0 0 1 18.9 11zM12 4.1c.9 1.2 1.8 3.6 1.9 6.9h-3.8c.1-3.3 1-5.7 1.9-6.9zM9.3 5.4A15 15 0 0 0 8.1 11h-3a8 8 0 0 1 4.2-5.6zM5.1 13h3a15 15 0 0 0 1.2 5.6A8 8 0 0 1 5.1 13zm6.9 6.9c-.9-1.2-1.8-3.6-1.9-6.9h3.8c-.1 3.3-1 5.7-1.9 6.9zm2.7-1.3a15 15 0 0 0 1.2-5.6h3a8 8 0 0 1-4.2 5.6z"/></svg>
      <span>www.mrtproperty.com</span>
    </li>
  </ul>

  <div class="address-tab">52 Kingsley Avenue Westmead</div>

  <svg class="front-stripes" viewBox="0 0 560 100" preserveAspectRatio="none" aria-hidden="true">
    <path d="M0 88 L560 70 L560 100 L0 100 Z" fill="var(--blue)"/>
    <path d="M0 90 L330 100 L0 100 Z" fill="var(--cyan)"/>
  </svg>
</section>

</body>
</html>
```